All-Natural Head Lice Removal company

I need a business card with my pre-existing logo. We are a new company located in Portland Oregon that goes into peoples homes to help with head lice removal. My products and approach are all- natural and also will be around children.On my current logo we used Teal Bl and the color Green. I am open to new ideas just want it simple and creative

Target Market(s)

my biggest market is families of school aged children

Industry/Entity Type

Business

Contact Information for Business Card

see upload for details from previous business card

Font styles to use
Serif

Colors
33a6d7
9bcb3b
f37122

Requirements
Must have
• Basic information/ logo put into a creative format that is catching to the eye
Nice to have
• creative

```html
<!DOCTYPE html>
<html lang="en">
<head>
<meta charset="utf-8">
<title>Willow Comb – Business Card</title>
<link href="https://fonts.googleapis.com/css2?family=Arvo:wght@400;700&display=swap" rel="stylesheet">
<style>
  :root {
    --page-bg: #e9ecef;
    --card-white: #ffffff;
    --brand-blue: #33a6d7;
    --brand-blue-deep: #1f86c8;
    --brand-green: #8cc63f;
    --ink: #2b2b2b;
    --edge-line: #1d2a33;
  }
  * { box-sizing: border-box; margin: 0; padding: 0; }
  html, body {
    width: 1200px; height: 913px; overflow: hidden;
    background: var(--page-bg);
    font-family: "Arvo", Georgia, serif;
    color: var(--ink);
  }
  .canvas { position: relative; width: 1200px; height: 913px; }
  .card {
    position: absolute; width: 540px; height: 309px;
    background: var(--card-white);
    overflow: hidden;
    box-shadow: 0 10px 28px rgba(0,0,0,.18);
  }
  .card--front { left: 45px; top: 302px; }
  .card--back  { left: 615px; top: 302px; }
  .card svg.band { position: absolute; inset: 0; }

  .tagline-top {
    position: absolute; left: 22px; top: 26px;
    display: flex; align-items: center; gap: 10px;
    font-size: 14px; font-weight: 700;
  }
  .tagline-top .marker { width: 12px; height: 12px; background: var(--brand-blue); }

  .brand {
    position: absolute; display: flex; align-items: center; gap: 12px;
    font-size: 30px; font-weight: 700; color: var(--ink);
  }
  .brand .dot {
    width: 58px; height: 58px; border-radius: 50%;
    background: var(--brand-green); border: 4px solid var(--brand-blue);
  }
  .card--front .brand { right: 26px; top: 58px; }
  .card--back .brand { left: 0; right: 0; top: 72px; justify-content: center; }

  .contact { position: absolute; left: 32px; top: 204px; color: #fff; }
  .contact .person { font-size: 19px; font-weight: 700; letter-spacing: .5px; line-height: 24px; }
  .contact .role { font-size: 10px; font-weight: 700; color: var(--ink); margin: 0 0 4px 12px; line-height: 14px; }
  .contact ul { list-style: none; margin-left: 12px; }
  .contact li { display: flex; align-items: center; gap: 8px; font-size: 12px; line-height: 17px; }
  .contact svg { width: 11px; height: 11px; fill: none; stroke: #fff; stroke-width: 2; }

  .back-copy {
    position: absolute; left: 0; right: 0; top: 172px;
    text-align: center; font-size: 13px; font-weight: 700; line-height: 18px;
  }
  .back-site {
    position: absolute; left: 0; right: 0; top: 238px; height: 34px;
    background: linear-gradient(90deg, var(--brand-blue-deep), var(--brand-blue) 40%);
    color: #fff; font-size: 13px; text-align: center; line-height: 34px;
  }
</style>
</head>
<body>
<main class="canvas">

  <section class="card card--front">
    <svg class="band" width="540" height="309" viewBox="0 0 540 309" aria-hidden="true">
      <defs>
        <linearGradient id="bandFill" x1="0" y1="0" x2="1" y2="1">
          <stop offset="0" stop-color="#2a93d0"/>
          <stop offset="1" stop-color="#5bbbe6"/>
        </linearGradient>
      </defs>
      <polygon points="0,195 540,130 540,309 0,309" fill="url(#bandFill)"/>
      <line x1="0" y1="195" x2="540" y2="130" stroke="var(--edge-line)" stroke-width="2"/>
    </svg>

    <div class="tagline-top"><span class="marker"></span>All Natural In-Home Lice Removal Services</div>

    <div class="brand"><span class="dot"></span>Willow Comb</div>

    <div class="contact">
      <div class="person">DANA WHITFIELD</div>
      <div class="role">OWNER</div>
      <ul>
        <li><svg viewBox="0 0 12 12"><path d="M2 1.5h2.5l1 2.5-1.5 1a6 6 0 0 0 3 3l1-1.5 2.5 1V10a1 1 0 0 1-1 1A9 9 0 0 1 1 2.5a1 1 0 0 1 1-1z"/></svg>1-855-555-COMB (2662)</li>
        <li><svg viewBox="0 0 12 12"><rect x="1" y="2.5" width="10" height="7"/><path d="M1 2.5l5 4 5-4"/></svg>Dana@WillowComb.com</li>
        <li><svg viewBox="0 0 12 12"><circle cx="6" cy="6" r="5"/><path d="M1 6h10M6 1c-2.5 3-2.5 7 0 10M6 1c2.5 3 2.5 7 0 10"/></svg>www.WillowComb.com</li>
      </ul>
    </div>
  </section>

  <section class="card card--back">
    <div class="brand"><span class="dot"></span>Willow Comb</div>
    <p class="back-copy">Try Willow Comb Today and Be Lice Free Tomorrow!<br>All Natural In-Home Lice Removal Services</p>
    <div class="back-site">www.WillowComb.com</div>
  </section>

</main>
</body>
</html>
```